QVR business card

Need a business card for a company that provides instructional design and elearning development services. The website is here: http://quorvane.studio/

I'm attaching a current logo, as well as the old business card design. While I like to keep it clean, the old design is too simplistic for my liking. The only idea I want to reuse from the old design is placing industry jargon on the back of the card, just need a better way to present it. But if you have other ideas for the back--feel free to experiment.

Please use the colors complementary to the color we have on the website. Thank you!

```html
<!DOCTYPE html>
<html lang="en">
<head>
<meta charset="utf-8">
<title>QVR business card</title>
<link rel="stylesheet" href="https://fonts.googleapis.com/css2?family=Open+Sans:wght@400;600;800&family=Fira+Sans+Extra+Condensed:wght@500&display=swap">
<style>
  :root {
    --teal: #14b3b0;
    --teal-dark: #0f9f9c;
    --gold: #d8c98e;
    --gold-deep: #c7b36b;
    --white: #ffffff;
    --ink: #2b2b2b;
    --backdrop: #2a2a2d;
  }
  * { margin: 0; padding: 0; box-sizing: border-box; }
  html, body { width: 1200px; height: 925px; overflow: hidden; background: var(--backdrop); }
  .canvas { position: relative; width: 1200px; height: 925px; }

  .card {
    position: absolute;
    width: 540px; height: 309px;
    overflow: hidden;
    border-radius: 2px;
    box-shadow: 0 10px 30px rgba(0,0,0,.45);
  }

  /* Back of card */
  .card-back { left: 40px; top: 170px; background: var(--teal); color: var(--white); }
  .back-question {
    position: absolute; left: 26px; top: 62px;
    font-family: "Open Sans", sans-serif; font-weight: 800;
    line-height: .98; text-transform: uppercase;
  }
  .back-question span { display: block; font-size: 42px; letter-spacing: .5px; }
  .back-question .emphasis { font-size: 62px; }
  .back-divider {
    position: absolute; left: 194px; top: 30px; bottom: 30px;
    width: 1.5px; background: rgba(255,255,255,.8);
  }
  .back-jargon {
    position: absolute; left: 210px; right: 16px; top: 34px;
    list-style: none;
    font-family: "Fira Sans Extra Condensed", sans-serif; font-weight: 500;
    font-size: 26px; line-height: 40px; text-transform: uppercase;
    white-space: nowrap;
  }

  /* Front of card */
  .card-front { left: 620px; top: 440px; background: var(--white); }
  .front-wave { position: absolute; inset: 0; }
  .brand {
    position: absolute; left: 70px; top: 92px;
    display: flex; align-items: center; gap: 12px;
  }
  .brand-dot { width: 26px; height: 26px; border-radius: 50%; background: var(--teal); }
  .brand-name {
    font-family: "Open Sans", sans-serif; font-weight: 600;
    font-size: 48px; color: var(--gold-deep); letter-spacing: 1px;
  }
  .holder { position: absolute; left: 54px; top: 236px; font-family: "Open Sans", sans-serif; }
  .holder-name { font-size: 15px; font-weight: 800; color: var(--gold); letter-spacing: .8px; text-transform: uppercase; }
  .holder-role { font-size: 13px; color: var(--ink); margin-top: 2px; }
  .contacts {
    position: absolute; left: 330px; top: 202px;
    list-style: none; font-family: "Open Sans", sans-serif;
    font-size: 12px; color: var(--white);
  }
  .contacts li { display: flex; align-items: center; gap: 7px; height: 22px; }
  .contact-icon { width: 15px; height: 15px; flex: none; }
</style>
</head>
<body>
<main class="canvas">

  <section class="card card-back" aria-label="Card back">
    <h2 class="back-question">
      <span>How</span>
      <span>Can</span>
      <span class="emphasis">We</span>
      <span>Help?</span>
    </h2>
    <div class="back-divider"></div>
    <ul class="back-jargon">
      <li>Mobile Learning SCORM</li>
      <li>Instructional Design LMS</li>
      <li>MOOCs eLearning HTML5</li>
      <li>Adult Learning Theory</li>
      <li>Gamification Classroom</li>
      <li>xAPI Blended Learning</li>
    </ul>
  </section>

  <section class="card card-front" aria-label="Card front">
    <svg class="front-wave" viewBox="0 0 540 309" width="540" height="309" aria-hidden="true">
      <path d="M0,222 C180,212 380,150 540,26 L540,309 L0,309 Z" fill="var(--teal)"/>
      <path d="M0,212 C180,202 380,140 540,16" fill="none" stroke="var(--white)" stroke-width="10"/>
      <path d="M0,206 C180,196 380,134 540,10" fill="none" stroke="var(--gold)" stroke-width="4"/>
      <path d="M148,197 L166,193 L160,208 Z" fill="var(--white)"/>
      <path d="M150,199 L164,196 L160,206" fill="none" stroke="var(--gold)" stroke-width="2"/>
    </svg>

    <div class="brand">
      <span class="brand-dot"></span>
      <span class="brand-name">QVR</span>
    </div>

    <div class="holder">
      <p class="holder-name">Marek Telvin</p>
      <p class="holder-role">Managing Director</p>
    </div>

    <ul class="contacts">
      <li>
        <svg class="contact-icon" viewBox="0 0 16 16" aria-hidden="true"><circle cx="8" cy="8" r="8" fill="var(--gold)"/><path d="M5.5 4.5l1.6 1.8-.8 1c.5 1 1.3 1.8 2.2 2.3l1-.8 1.8 1.6-.9 1.1C8.6 11.3 5 7.8 4.5 5.4z" fill="var(--white)"/></svg>
        555-014-2287
      </li>
      <li>
        <svg class="contact-icon" viewBox="0 0 16 16" aria-hidden="true"><circle cx="8" cy="8" r="8" fill="var(--gold)"/><rect x="4" y="5.5" width="8" height="5.5" fill="none" stroke="var(--white)" stroke-width="1.2"/><path d="M4 5.5l4 3 4-3" fill="none" stroke="var(--white)" stroke-width="1.2"/></svg>
        mtelvin@quorvane.studio
      </li>
      <li>
        <svg class="contact-icon" viewBox="0 0 16 16" aria-hidden="true"><circle cx="8" cy="8" r="8" fill="var(--gold)"/><circle cx="8" cy="8" r="4" fill="none" stroke="var(--white)" stroke-width="1.1"/><path d="M4 8h8M8 4c-2 2.5-2 5.5 0 8M8 4c2 2.5 2 5.5 0 8" fill="none" stroke="var(--white)" stroke-width="1"/></svg>
        www.quorvane.studio
      </li>
    </ul>
  </section>

</main>
</body>
</html>
```